Allied Health team of Physiotherapists & Occupational Therapists seek a business card design

We have our new logo, we now need our new business cards and stationary. Tidewell: Oedema & Family Clinic is seeking a generic card design to represent our whole team and individual cards for each therapist that incorporates our new logo to communicate our holistic approach that is calming, nuturing, supportive and welcoming.
Our Physiotherapists and Occupational Therapists assess, treat and provide education for people who are at risk of or who have lymphoedema. This is often as a result of treatment for cancer. We provide pre-operative and post-operative management and cancer rehabilitation in our Pilates studio. Our team also consists of Physiotherapists who have a strong interest in pelvic floor and continence management for both men and women.

Target Market(s)

Mainly women health conscious

Industry/Entity Type

Allied Health: Physiotherapy / Occupational Therapy

Contact Information for Business Card

Address: 14 Gallivant Ave Frankston 3199 Phone: 84316570 fax: 8431 6578 Email: info@tidewellcareservices.com.au Website: tidewellcareservices.com.au Facebook address: facebook.com/TidewellOedemaAndFamilyCareClinic. Room to write appointments. Individual cards need to have name, office email and individual email and professional details

Requirements
Must have
• Logo as per uploaded documents

```html
<!DOCTYPE html>
<html lang="en">
<head>
<meta charset="utf-8">
<title>Tidewell Business Card</title>
<link href="https://fonts.googleapis.com/css2?family=Arimo&family=Carlito&display=swap" rel="stylesheet">
<style>
  :root {
    --backdrop: #ece8e3;
    --peach: #f8b088;
    --paper: #ffffff;
    --sage: #c6d1c9;
    --logo-peach: #eeb286;
    --ink-light: #ffffff;
  }
  * { margin: 0; padding: 0; box-sizing: border-box; }
  html, body {
    width: 1200px; height: 960px; overflow: hidden;
    background: var(--backdrop);
    font-family: "Carlito", "Calibri", sans-serif;
  }
  .card {
    position: absolute; width: 601px; height: 343px;
    box-shadow: 0 2px 6px rgba(0,0,0,.25);
    overflow: hidden;
  }
  .card-front { left: 313px; top: 129px; background: var(--paper); }
  .card-back { left: 312px; top: 488px; background: var(--peach); }

  .contact-panel {
    position: absolute; left: 0; top: 42px; width: 284px; height: 260px;
    background: var(--peach); color: var(--ink-light);
  }
  .person-name {
    position: absolute; left: 28px; top: 54px;
    font-family: "Arimo", "Arial", sans-serif; font-size: 18px; letter-spacing: .2px;
  }
  .person-role { position: absolute; left: 29px; top: 76px; font-size: 10px; }
  .contact-list { position: absolute; left: 29px; top: 121px; list-style: none; }
  .contact-list li {
    display: flex; align-items: center; height: 28px; font-size: 13px;
  }
  .contact-list svg { width: 14px; height: 14px; margin-right: 9px; }

  .side-tab {
    position: absolute; left: 582px; top: 49px; width: 30px; height: 241px;
    background: var(--sage); border-radius: 22px 0 0 22px;
  }

  .brand-mark {
    position: absolute; width: 150px; height: 150px; border-radius: 50%;
    display: flex; flex-direction: column; align-items: center; justify-content: center;
    text-align: center; font-size: 13px; line-height: 1.25;
  }
  .brand-mark .brand-name { font-size: 30px; line-height: 1.1; }
  .card-front .brand-mark {
    left: 359px; top: 99px; color: var(--logo-peach);
    border: 2px solid var(--logo-peach);
  }
  .card-back .brand-mark {
    left: 225px; top: 96px; color: var(--ink-light);
    border: 2px solid var(--ink-light);
  }
  .website {
    position: absolute; left: 0; right: 0; top: 297px; text-align: center;
    color: var(--ink-light); font-size: 17px; letter-spacing: 3.6px;
  }
</style>
</head>
<body>
  <section class="card card-front">
    <div class="contact-panel">
      <h1 class="person-name">ALEX HARLOW</h1>
      <p class="person-role">CEO/Managing Director</p>
      <ul class="contact-list">
        <li>
          <svg viewBox="0 0 16 16" fill="none" stroke="#fff" stroke-width="1.5"><path d="M4 1.5l2.5 3-1.5 2a9 9 0 0 0 4.5 4.5l2-1.5 3 2.5-1.5 2.5C7 14 2 9 1.5 3z"/></svg>
          301-555-0147
        </li>
        <li>
          <svg viewBox="0 0 16 16" fill="#fff"><rect x="4" y="1" width="8" height="4"/><rect x="1" y="5" width="14" height="7" rx="1"/><rect x="4" y="9" width="8" height="6" fill="#fff" stroke="#f8b088"/></svg>
          301-555-0147
        </li>
        <li>
          <svg viewBox="0 0 16 16" fill="none" stroke="#fff" stroke-width="1.4"><rect x="1" y="3" width="14" height="10"/><path d="M1 3l7 6 7-6M1 13l5-5M15 13l-5-5"/></svg>
          alexharlow@tidewellcare.com
        </li>
      </ul>
    </div>
    <div class="brand-mark">
      <span class="brand-name">Tidewell</span>
      <span>Oedema &amp; Family Clinic</span>
    </div>
    <div class="side-tab"></div>
  </section>

  <section class="card card-back">
    <div class="brand-mark">
      <span class="brand-name">Tidewell</span>
      <span>Oedema &amp; Family Clinic</span>
    </div>
    <p class="website">www.tidewellcareservices.com.au</p>
  </section>
</body>
</html>
```